Business Intelligence Application - Reporting Menu and Report Criteria Design

Looking for a fresh, effective and user friendly view for the menu structure and reporting criteria screen format for a business reporting application. Initial format completed, content structure is in place, but we need the 'wow' design.. as its a serious professional report/BI tool it has to fall within certain guidelines for clarity and graphics..but we want it to be slick, friendly, great user experience. There is a large amount of complex content to fit into a small space and we need it to be very inviting, modern and intuitive.. If interested, please review the attachment. We have live screens in operation, but feel these could be improved and looking forward to seeing what great creative suggestions could be made. Please review work done to date in the attached.. We are not looking for a total re-design of everything, all the basic business content/structure is there.. but tell us what we could do to improve this in terms of graphic design... particularly the criteria screens.. thanks!
Updates

Reason: Need a few more days to review designs - thanks for all submissions so far, we will make a selection shortly.

Target Market(s)

Business analysts, hotel operations teams, finance analysts hospitality industry

Industry/Entity Type

Hospitality

Coding

Coded - Design and coding required

Number of Pages Required

4 page

Font styles to use
Sans Serif
Other font styles liked:
• Candara, please see example in deck

Colors
3276b5
3176b5
0255a3
85acd3
33a6d7
cee9f5
85cae6

Requirements
Must have
• sharp clear, logical menu structure, (currently it has 'clicks to sub-menus, we need hover over, slide to sub-menus..) colour, styling.. and most focus on revision of criteria.. right now is somewhat heavy, cumbersome.. keep colour and friendly intuitive process steps.. its heavy analytical stuff.. best of luck!
Should not have
• No grey fonts on white or grey screens! many business apps are not readable or sharp.. or fonts are too small.. colourless, so please avoid that.. see our deck - sharp dark (navy) or black fonts on white, or light shading..

```html
<!DOCTYPE html>
<html lang="en">
<head>
<meta charset="utf-8">
<title>Yield Desk – Property Search</title>
<link href="https://fonts.googleapis.com/css2?family=Roboto:wght@400;500&display=swap" rel="stylesheet">
<style>
:root{
  --navy-deep:#041937;
  --navy:#06214a;
  --navy-item:#092a58;
  --blue:#0255a3;
  --sky:#33a6d7;
  --page:#ebedf1;
  --white:#ffffff;
  --field:#f6f7f9;
  --field-line:#d6d9de;
  --ink:#0e1e33;
  --muted:#4d5562;
}
*{box-sizing:border-box;margin:0;padding:0}
html,body{width:1200px;height:817px;overflow:hidden}
body{font-family:'Roboto',Arial,sans-serif;background:var(--page);position:relative;color:var(--ink)}
.sidebar{position:absolute;left:0;top:0;width:218px;height:817px;background:var(--navy-deep)}
.brand{height:85px;display:flex;align-items:center;padding-left:34px;gap:14px;background:var(--navy)}
.brand-dot{width:26px;height:26px;border-radius:50%;background:var(--sky)}
.brand-name{color:var(--white);font-size:24px;font-weight:500;letter-spacing:.2px}
.menu{list-style:none}
.menu-item{display:flex;height:53px;background:var(--navy-item);border-bottom:1px solid var(--navy-deep)}
.menu-icon{width:63px;flex:none;display:flex;align-items:center;justify-content:center;border-right:1px solid var(--navy-deep)}
.menu-label{flex:1;display:flex;align-items:center;justify-content:space-between;padding:0 18px 0 11px;color:var(--white);font-size:15.5px;white-space:nowrap;gap:6px}
.menu-item.active .menu-icon{background:var(--sky)}
.menu-item.active .menu-label{background:var(--blue)}
.topbar{position:absolute;left:218px;top:0;right:0;height:83px;background:var(--white);display:flex;align-items:center;justify-content:flex-end;padding-right:64px;gap:14px}
.welcome{font-size:14.5px;font-weight:500;color:#3b4350}
.date{font-size:13.5px;color:#3b4350}
.sep{color:#6b7280;font-size:13px}
.panel{position:absolute;left:276px;top:124px;width:469px;height:552px;background:var(--white);box-shadow:0 1px 3px rgba(0,0,0,.15)}
.panel-head{height:46px;background:var(--blue);color:var(--white);display:flex;align-items:center;padding-left:20px;gap:8px;font-size:20px}
.row-label{position:absolute;left:34px;font-size:15.5px;line-height:18px;color:var(--ink)}
.field{position:absolute;left:172px;width:256px;height:45px;background:var(--field);border:1px solid var(--field-line);box-shadow:0 2px 3px rgba(0,0,0,.12);font-size:13px;color:var(--muted);display:flex;align-items:center;padding-left:15px}
.suggestion{position:absolute;left:172px;width:256px;height:38px;background:#eceef1;border:1px solid var(--field-line);font-size:13px;color:var(--muted);display:flex;align-items:center;padding-left:15px}
.caret{position:absolute;right:16px;top:19px}
.next-btn{position:absolute;left:341px;top:487px;width:87px;height:34px;background:var(--sky);color:var(--white);font-size:15px;display:flex;align-items:center;justify-content:center;gap:3px;border-radius:2px}
.footer{position:absolute;left:0;right:0;top:770px;height:47px;background:var(--navy-deep);color:var(--white);font-size:12px}
.footer .copy{position:absolute;left:507px;top:17px}
.footer .code{position:absolute;left:1159px;top:18px;font-size:11.5px}
</style>
</head>
<body>
<aside class="sidebar">
  <div class="brand"><span class="brand-dot"></span><span class="brand-name">Yield Desk</span></div>
  <ul class="menu">
    <li class="menu-item"><span class="menu-icon"><svg width="16" height="18" viewBox="0 0 16 18" fill="#fff"><circle cx="8" cy="5" r="4.5"/><path d="M0 18c0-5 3-8 8-8s8 3 8 8z"/></svg></span><span class="menu-label">Admin<svg width="8" height="13" viewBox="0 0 8 13"><path d="M1 1l5.5 5.5L1 12" stroke="#fff" stroke-width="2" fill="none"/></svg></span></li>
    <li class="menu-item"><span class="menu-icon"><svg width="18" height="14" viewBox="0 0 18 14"><path d="M3 1h12l3 7v5H0V8z" fill="#fff"/><path d="M2.5 8h4l1 2h3l1-2h4" stroke="#092a58" stroke-width="1.6" fill="none"/></svg></span><span class="menu-label">Management<svg width="8" height="13" viewBox="0 0 8 13"><path d="M1 1l5.5 5.5L1 12" stroke="#fff" stroke-width="2" fill="none"/></svg></span></li>
    <li class="menu-item active"><span class="menu-icon"><svg width="18" height="15" viewBox="0 0 18 15" fill="#fff"><path d="M9 0l9 8h-3v7h-4v-5H7v5H3V8H0z"/></svg></span><span class="menu-label">Property Search<svg width="8" height="13" viewBox="0 0 8 13"><path d="M1 1l5.5 5.5L1 12" stroke="#fff" stroke-width="2" fill="none"/></svg></span></li>
    <li class="menu-item"><span class="menu-icon"><svg width="21" height="18" viewBox="0 0 21 18"><rect x="1" y="1" width="19" height="12" fill="none" stroke="#fff" stroke-width="2"/><rect x="8" y="13" width="5" height="3" fill="#fff"/><rect x="5" y="16" width="11" height="2" fill="#fff"/></svg></span><span class="menu-label">Intel<svg width="8" height="13" viewBox="0 0 8 13"><path d="M1 1l5.5 5.5L1 12" stroke="#fff" stroke-width="2" fill="none"/></svg></span></li>
    <li class="menu-item"><span class="menu-icon"><svg width="16" height="19" viewBox="0 0 16 19"><path d="M0 0h10l6 6v13H0z" fill="#fff"/><path d="M3 9h10M3 12h10M3 15h10" stroke="#092a58" stroke-width="1.5"/></svg></span><span class="menu-label">Planning<svg width="8" height="13" viewBox="0 0 8 13"><path d="M1 1l5.5 5.5L1 12" stroke="#fff" stroke-width="2" fill="none"/></svg></span></li>
  </ul>
</aside>

<header class="topbar">
  <span class="welcome">Welcome Admin</span>
  <span class="sep">|</span>
  <span class="date">Tuesda October 03 ,2017</span>
  <span class="sep">|</span>
  <svg width="15" height="16" viewBox="0 0 15 16" fill="#0a1f44"><path d="M7.5 0C4.5 0 3 2.5 3 5v4L0 12h15l-3-3V5c0-2.5-1.5-5-4.5-5z"/><circle cx="7.5" cy="14" r="2"/></svg>
  <span class="sep">|</span>
  <svg width="16" height="14" viewBox="0 0 16 14"><path d="M6 1H1v12h5" stroke="#0a1f44" stroke-width="2" fill="none"/><path d="M7 4h4V0l5 7-5 7v-4H7z" fill="#0a1f44"/></svg>
</header>

<main class="panel">
  <div class="panel-head"><svg width="20" height="16" viewBox="0 0 18 15" fill="#fff"><path d="M9 0l9 8h-3v7h-4v-5H7v5H3V8H0z"/></svg>Property Search</div>

  <span class="row-label" style="top:93px">Search Name</span>
  <div class="field" style="top:81px">Coral....</div>
  <div class="suggestion" style="top:126px">Coral Bay Hotel</div>

  <span class="row-label" style="top:185px">Search ID</span>
  <div class="field" style="top:174px"></div>

  <span class="row-label" style="top:248px;left:33px">Search Product</span>
  <div class="field" style="top:236px"></div>

  <span class="row-label" style="top:310px;left:33px">Divisions</span>
  <div class="field" style="top:298px">North America<svg class="caret" width="10" height="6" viewBox="0 0 10 6"><path d="M0 0h10L5 6z" fill="#222"/></svg></div>

  <span class="row-label" style="top:372px">Regions</span>
  <div class="field" style="top:360px"></div>

  <span class="row-label" style="top:433px">Areas</span>
  <div class="field" style="top:422px"></div>

  <div class="next-btn">Next<svg width="11" height="10" viewBox="0 0 11 10"><path d="M1 1l4 4-4 4M6 1l4 4-4 4" stroke="#fff" stroke-width="1.6" fill="none"/></svg></div>
</main>

<footer class="footer"><span class="copy">Copyright © 2017. All Rights Reserved</span><span class="code">C6</span></footer>
</body>
</html>
```